Tellmora Corporate Stationery

Look for design of all new corporate stationery for an existing insurance broking business that is going through a redesign and move from older partners to younger family members. New Logo is attached. Company is Brisbane based.
Colours in the Logo is Hex #43bed8 and website features a lot of hex #17b8d8. Website front page "A plan to protect you" - headline. "Professional and Individual advice to protect your greatest assets" - tagline.

Stationery required: Business Cards, Letter head, Thank-you cards, Birthday cards, Presentation folders, With Compliment slips and a powerpoint template. We also would like to send a card to all customers with the something along of the lines of "something new".

Target Market(s)

Customers of Insurance business looking at superannuation, life and income protection insurance, investment advice and wills

Industry/Entity Type

Insurance Broker

Font styles to use
Other font styles liked:
• same as logo

Requirements
Must have
• The above designs for new stationery for the new business including:
• Business Cards, Letter head, Thank-you cards, Birthday cards, Presentation folders, With Compliment slips and a powerpoint template. We also would like to send a card to all customers with the something along of the lines of "something new".
Nice to have
• It is a new look - long time family business being passed to next generation - big focus on advice for YOU, individual advice etc..

```html
<!DOCTYPE html>
<html lang="en">
<head>
<meta charset="utf-8">
<title>Tellmora Corporate Stationery</title>
<link href="https://fonts.googleapis.com/css2?family=Open+Sans:wght@400;600;700&family=Roboto+Condensed:wght@400;700&family=Raleway:wght@300;400&display=swap" rel="stylesheet">
<style>
  :root {
    --brand: #3fbfd8;
    --brand-deep: #35adc6;
    --grey: #7a7b7d;
    --grey-dark: #4f5052;
    --ink: #6d6e70;
    --paper: #f8f8f8;
    --page: #ececec;
    --rule: #cfd0d1;
    --ghost: rgba(0,0,0,0.035);
    --ghost-light: rgba(255,255,255,0.1);
  }
  * { box-sizing: border-box; margin: 0; padding: 0; }
  html, body { width: 1028px; height: 1200px; overflow: hidden; }
  body { background: var(--page); font-family: "Open Sans", sans-serif; color: var(--ink); position: relative; }
  .item { position: absolute; overflow: hidden; box-shadow: 0 1px 4px rgba(0,0,0,0.12); }
  .brand-name { font-family: "Open Sans", sans-serif; font-weight: 600; letter-spacing: 0.08em; text-transform: uppercase; white-space: nowrap; }
  .ghost-disc { position: absolute; border-radius: 50%; background: var(--ghost); }
  .stripe { position: absolute; left: 0; right: 0; bottom: 0; height: 3px; background: linear-gradient(90deg, var(--brand) 0 75%, var(--grey) 75% 100%); }

  /* Letterhead */
  .letterhead { left: 217px; top: 94px; width: 280px; height: 394px; background: var(--paper); }
  .letterhead .brand-name { position: absolute; top: 44px; width: 100%; text-align: center; color: var(--brand); font-size: 11px; }
  .letterhead .ghost-disc { left: 52px; top: 112px; width: 168px; height: 168px; }
  .letterhead .footer { position: absolute; bottom: 10px; width: 100%; text-align: center; font-size: 4.6px; line-height: 1.6; color: var(--grey); }
  .letterhead .footer b { color: var(--brand); font-weight: 600; }

  /* Presentation folder */
  .folder { left: 544px; top: 76px; width: 332px; height: 418px; background: var(--brand); }
  .folder::before { content: ""; position: absolute; left: 0; top: 0; bottom: 0; width: 8px; background: var(--brand-deep); }
  .folder .ghost-disc { left: 40px; top: 50px; width: 300px; height: 300px; background: var(--ghost-light); }
  .folder .brand-name { position: absolute; top: 222px; width: 100%; text-align: center; color: #fff; font-size: 27px; letter-spacing: 0.1em; }
  .folder .tag { position: absolute; top: 258px; width: 100%; text-align: center; color: #fff; font-size: 12px; letter-spacing: 0.12em; text-transform: uppercase; }

  /* Business cards */
  .card-front { left: 116px; top: 526px; width: 126px; height: 70px; background: var(--paper); }
  .card-front .ghost-disc { left: -10px; top: -14px; width: 52px; height: 52px; }
  .card-front .brand-name { position: absolute; right: 8px; top: 12px; color: var(--brand); font-size: 7px; }
  .card-front .person { position: absolute; left: 6px; top: 27px; font-size: 3.8px; line-height: 1.3; }
  .card-front .person strong { color: var(--brand); font-weight: 600; font-size: 4.6px; }
  .card-front .address { position: absolute; right: 6px; top: 46px; font-size: 3.6px; text-align: right; line-height: 1.3; }
  .card-front .stripe { height: 2px; }
  .card-back { left: 116px; top: 618px; width: 126px; height: 70px; background: var(--brand); }
  .card-back .brand-name { position: absolute; top: 29px; width: 100%; text-align: center; color: #fff; font-size: 9px; }

  /* Compliment slip */
  .slip { left: 275px; top: 536px; width: 313px; height: 150px; background: var(--paper); }
  .slip .brand-name { position: absolute; left: 16px; top: 30px; color: var(--brand); font-size: 9px; }
  .slip .address { position: absolute; left: 16px; top: 44px; font-size: 5px; line-height: 1.4; }
  .slip .ghost-disc { left: 172px; top: 16px; width: 118px; height: 118px; }

  /* Envelope */
  .envelope { left: 618px; top: 536px; width: 314px; height: 150px; background: var(--paper); }
  .envelope svg { position: absolute; left: 0; top: 0; }
  .envelope .web { position: absolute; top: 36px; width: 100%; text-align: center; color: #fff; font-size: 5px; }
  .envelope .flap-dot { position: absolute; left: 148px; top: 14px; width: 18px; height: 18px; border-radius: 50%; border: 2px solid rgba(255,255,255,0.9); }

  /* Slides */
  .slide { width: 257px; height: 193px; background: var(--paper); }
  .slide .head { position: absolute; left: 14px; right: 14px; top: 12px; border-bottom: 1px solid var(--rule); padding-bottom: 2px; }
  .slide .head h2 { font-family: "Roboto Condensed", sans-serif; font-weight: 400; color: var(--brand); font-size: 12px; line-height: 1.1; }
  .slide .head p { font-size: 6px; color: var(--grey); }
  .slide .head .mark { position: absolute; right: 0; top: 2px; width: 11px; height: 11px; border-radius: 50%; background: var(--grey); }
  .body-text { font-size: 3.8px; line-height: 1.55; color: var(--grey-dark); }

  .slide-title { left: 102px; top: 733px; }
  .slide-title .brand-name { position: absolute; top: 58px; width: 100%; text-align: center; color: var(--brand); font-size: 18px; }
  .slide-title .tag { position: absolute; top: 83px; width: 100%; text-align: center; color: var(--grey); font-size: 9px; letter-spacing: 0.1em; text-transform: uppercase; }
  .slide-title svg { position: absolute; left: 0; top: 122px; }
  .slide-title .welcome { position: absolute; left: 0; width: 230px; top: 128px; text-align: center; color: #fff; font-family: "Roboto Condensed", sans-serif; line-height: 1.25; }
  .welcome .w1 { font-size: 14px; }
  .welcome .w2 { font-size: 16px; font-weight: 700; }
  .welcome .w3 { font-size: 13px; }

  .slide-team { left: 383px; top: 733px; }
  .team { position: absolute; left: 19px; top: 54px; display: flex; gap: 8px; }
  .member { width: 50px; }
  .photo { width: 50px; height: 50px; background: var(--grey-dark); border: 2px solid #d8d8d8; color: #ddd; font-size: 6px; display: flex; align-items: center; justify-content: center; }
  .member h3 { margin-top: 14px; font-size: 5px; font-weight: 400; color: var(--brand); }
  .member .role { font-size: 4.5px; color: var(--grey); margin-bottom: 6px; }

  .slide-groups { left: 670px; top: 733px; }
  .groups { position: absolute; left: 16px; right: 16px; top: 52px; display: grid; grid-template-columns: 1fr 1fr; column-gap: 10px; row-gap: 9px; }
  .groups h3 { font-size: 5.5px; font-weight: 400; color: var(--brand); margin-bottom: 3px; }

  .slide-bars { left: 102px; top: 938px; }
  .slide-bars svg { position: absolute; left: 22px; top: 46px; }
  .slide-bars .side { position: absolute; left: 156px; top: 50px; width: 80px; }
  .slide-bars .side p + p { margin-top: 5px; }
  .slide-bars .bottom { position: absolute; left: 20px; right: 20px; top: 143px; }

  .slide-pie { left: 383px; top: 938px; }
  .slide-pie .left { position: absolute; left: 20px; top: 62px; width: 110px; text-align: center; }
  .slide-pie .left p + p { margin-top: 8px; }
  .slide-pie svg { position: absolute; left: 155px; top: 55px; }
  .legend { position: absolute; left: 157px; top: 126px; font-size: 3.8px; color: var(--grey-dark); line-height: 2; }
  .legend span { display: inline-block; width: 5px; height: 5px; margin-right: 3px; vertical-align: -1px; }
  .slide-pie .note { position: absolute; left: 157px; top: 148px; width: 80px; }

  .slide-thanks { left: 670px; top: 938px; background: var(--brand); }
  .slide-thanks .ghost-disc { left: 40px; top: -20px; width: 200px; height: 200px; background: var(--ghost-light); }
  .slide-thanks h2 { position: absolute; left: 0; right: 0; top: 60px; text-align: center; font-family: "Raleway", sans-serif; font-weight: 400; color: #fff; font-size: 44px; line-height: 1; }
  .slide-thanks .sub { position: absolute; left: 0; right: 0; top: 102px; text-align: center; font-family: "Raleway", sans-serif; font-weight: 400; color: #fff; font-size: 23px; }
  .slide-thanks .footer { position: absolute; bottom: 16px; width: 100%; text-align: center; color: #fff; font-size: 4.2px; line-height: 1.6; }
</style>
</head>
<body>

<section class="item letterhead" aria-label="Letterhead">
  <div class="ghost-disc"></div>
  <div class="brand-name">Tellmora</div>
  <div class="footer">
    412 Harbour Row, Brisbane QLD 4000 | <b>P:</b> 07 3100 2200<br>
    <b>M:</b> 0400 118 220 <b>F:</b> 07 3100 2201 <b>E:</b> hello@tellmora.com <b>W:</b> www.tellmora.com
  </div>
  <div class="stripe"></div>
</section>

<section class="item folder" aria-label="Presentation folder">
  <div class="ghost-disc"></div>
  <div class="brand-name">Tellmora</div>
  <div class="tag">Financial Group</div>
</section>

<section class="item card-front" aria-label="Business card front">
  <div class="ghost-disc"></div>
  <div class="brand-name">Tellmora</div>
  <div class="person"><strong>DANA REYES</strong><br>Founder<br>07 3100 2200<br>0400 118 220<br>07 3100 2201<br>hello@tellmora.com</div>
  <div class="address">412 Harbour Row<br>Brisbane QLD 4000<br>www.tellmora.com</div>
  <div class="stripe"></div>
</section>

<section class="item card-back" aria-label="Business card back">
  <div class="brand-name">Tellmora</div>
</section>

<section class="item slip" aria-label="With compliments slip">
  <div class="ghost-disc"></div>
  <div class="brand-name">Tellmora</div>
  <div class="address">412 Harbour Row,<br>Brisbane QLD 4000</div>
  <div class="stripe"></div>
</section>

<section class="item envelope" aria-label="Envelope">
  <svg width="314" height="150" viewBox="0 0 314 150" aria-hidden="true">
    <polygon points="0,0 314,0 314,20 300,50 14,50 0,20" fill="var(--brand)"/>
  </svg>
  <div class="flap-dot"></div>
  <div class="web">www.tellmora.com</div>
</section>

<section class="item slide slide-title" aria-label="Title slide">
  <div class="brand-name">Tellmora</div>
  <div class="tag">Financial Group</div>
  <svg width="257" height="71" viewBox="0 0 257 71" aria-hidden="true">
    <rect width="257" height="71" fill="var(--brand)"/>
    <polygon points="232,0 257,0 257,71 213,71" fill="var(--grey)"/>
  </svg>
  <div class="welcome">
    <div class="w1">Welcome to Our</div>
    <div class="w2">Presentation Name</div>
    <div class="w3">Description</div>
  </div>
</section>

<section class="item slide slide-team" aria-label="Team slide">
  <div class="head"><h2>Heading Here</h2><p>Sub Heading</p><span class="mark"></span></div>
  <div class="team">
    <div class="member"><div class="photo" role="img" aria-label="Team member portrait">Photo</div><h3>Team member1</h3><p class="role">Title</p><p class="body-text">Leads client advice on cover, super and long term plans.</p></div>
    <div class="member"><div class="photo" role="img" aria-label="Team member portrait">Photo</div><h3>Team member2</h3><p class="role">Title</p><p class="body-text">Guides families through life and income protection choices.</p></div>
    <div class="member"><div class="photo" role="img" aria-label="Team member portrait">Photo</div><h3>Team member3</h3><p class="role">Title</p><p class="body-text">Builds investment plans that grow with each client.</p></div>
    <div class="member"><div class="photo" role="img" aria-label="Team member portrait">Photo</div><h3>Team member4</h3><p class="role">Title</p><p class="body-text">Helps clients put wills and estate plans in order.</p></div>
  </div>
</section>

<section class="item slide slide-groups" aria-label="Services slide">
  <div class="head"><h2>Heading Here</h2><p>Sub Heading</p><span class="mark"></span></div>
  <div class="groups">
    <div><h3>Group1</h3><p class="body-text">Life cover reviewed each year so your family stays protected as life changes.</p></div>
    <div><h3>Group4</h3><p class="body-text">Investment plans built around your goals, your timeline and your comfort with risk.</p></div>
    <div><h3>Group2</h3><p class="body-text">Income protection that keeps bills paid while you recover and return to work.</p></div>
    <div><h3>Group5</h3><p class="body-text">Wills and estate planning so your wishes are clear and your assets are safe.</p></div>
    <div><h3>Group3</h3><p class="body-text">Superannuation advice to help your savings work harder until the day you retire.</p></div>
    <div><h3>Group6</h3><p class="body-text">One adviser who knows your story and answers the phone when you call.</p></div>
  </div>
</section>

<section class="item slide slide-bars" aria-label="Bar chart slide">
  <div class="head"><h2>Heading Here</h2><p>Sub Heading</p><span class="mark"></span></div>
  <svg width="108" height="82" viewBox="0 0 108 82" aria-hidden="true">
    <g stroke="#d6d6d6" stroke-width="0.6">
      <line x1="0" y1="4" x2="108" y2="4"/><line x1="0" y1="14" x2="108" y2="14"/><line x1="0" y1="24" x2="108" y2="24"/>
      <line x1="0" y1="34" x2="108" y2="34"/><line x1="0" y1="44" x2="108" y2="44"/><line x1="0" y1="54" x2="108" y2="54"/>
      <line x1="0" y1="64" x2="108" y2="64"/><line x1="0" y1="74" x2="108" y2="74"/>
    </g>
    <g fill="var(--brand)">
      <rect x="8" y="2" width="12" height="76"/><rect x="27" y="11" width="12" height="67"/>
      <rect x="46" y="30" width="12" height="48"/><rect x="65" y="16" width="12" height="62"/>
    </g>
    <g fill="#fff" font-size="4" font-family="Open Sans, sans-serif">
      <text transform="translate(16 74) rotate(-90)">Year 1</text><text transform="translate(35 74) rotate(-90)">Year 2</text>
      <text transform="translate(54 74) rotate(-90)">Year 3</text><text transform="translate(73 74) rotate(-90)">Year 4</text>
    </g>
  </svg>
  <div class="side body-text">
    <p>Client numbers have grown steadily over four years as families return for reviews and refer friends and relatives.</p>
    <p>Most new clients come to us through a recommendation from someone we already help.</p>
  </div>
  <p class="bottom body-text">Each bar shows a year of growth across life, income protection, super and investment advice, measured by active client plans.</p>
</section>

<section class="item slide slide-pie" aria-label="Pie chart slide">
  <div class="head"><h2>Heading Here</h2><p>Sub Heading</p><span class="mark"></span></div>
  <div class="left body-text">
    <p>Advice is shaped around each person rather than a product. We listen first, explain options in plain language and review your plan as your family and work change over time.</p>
    <p>Every plan is checked each year and updated whenever your circumstances shift.</p>
  </div>
  <svg width="60" height="60" viewBox="-30 -30 60 60" aria-hidden="true">
    <path d="M0,0 L0,-28 A28,28 0 0,1 24.2,-14 Z" fill="var(--grey)" stroke="#fff" stroke-width="0.8"/>
    <path d="M0,0 L24.2,-14 A28,28 0 0,1 27.5,5 Z" fill="var(--brand)" stroke="#fff" stroke-width="0.8"/>
    <path d="M0,0 L27.5,5 A28,28 0 0,1 10,26 Z" fill="var(--grey)" stroke="#fff" stroke-width="0.8"/>
    <path d="M0,0 L10,26 A28,28 0 1,1 0,-28 Z" fill="var(--brand)" stroke="#fff" stroke-width="0.8"/>
  </svg>
  <div class="legend">
    <div><span style="background:var(--brand)"></span>Life and income cover 50%</div>
    <div><span style="background:var(--grey)"></span>Super and investment 50%</div>
  </div>
  <p class="note body-text">Share of client plans by type of advice.</p>
</section>

<section class="item slide slide-thanks" aria-label="Closing slide">
  <div class="ghost-disc"></div>
  <h2>Thanks</h2>
  <div class="sub">For Coming</div>
  <div class="footer">
    412 Harbour Row, Brisbane QLD 4000 | P: 07 3100 2200<br>
    M: 0400 118 220 F: 07 3100 2201 E: hello@tellmora.com W: www.tellmora.com
  </div>
</section>

</body>
</html>
```